Strategy and Technology Consulting - Our Story and Values Page

Interior Page design – Our History and Our Values

Our homepage has been designed and we are looking for a design for one of the interior pages. This interior page tells the story of Our History and Our Values

Because the homepage has been designed, we would like this interior page to reflect the design of the homepage without being a mirror image of the homepage.

This site will be implemented in WordPress using the Elementor framework.

Font: Poppins medium and Poppins dark
Illustrations: Our homepage illustrations were designed by “Brelin 1974” on Quillmark. Compatible original or stock illustrations are welcome. Stock photography is also welcome. Brelin is also available through Brelin Tosamek on Ravolo

Uploaded Files
• Homepage design – this is the design we will use for our homepage. Contest entries should reflect this basic style but should be distinctly different from the homepage.
• Our History and Our Values – Wireframe – the basic layout of the page we are looking for.
• Our History and Our Values – Word document with the text supporting the wireframe.
• Color Palette – please use colors compatible with the palette attached.

Our Story - timeline
There is a timeline element in the wireframe. The wireframe displays this as a series of chevrons (arrows), but it does not need to be. Creativity in display of the timeline is appreciated.

Our Values
If you look at the Word document, you will see that there are a lot of words on the page. The winning design will present the information in a way that engages the user without overwhelming them with too much to read. For example, they may click on a value and see more information.

Target Market(s)

CIO's and Technology Executives

Number of Pages Required

1 page

Font styles to use
Sans Serif
Other font styles liked:
• Poppin

Requirements
Must have
• A timeline element, all of our values
Nice to have
• Clever timeline display

```html
<!DOCTYPE html>
<html lang="en">
<head>
<meta charset="utf-8">
<title>Veltrano – Our Story &amp; Values</title>
<link href="https://fonts.googleapis.com/css2?family=Poppins:wght@400;500;600;700&display=swap" rel="stylesheet">
<style>
:root{
  --blue-dark:#1d4a80;
  --blue:#2d68a4;
  --blue-light:#dbe7f4;
  --yellow:#f2b705;
  --white:#ffffff;
  --ink:#1f2a3c;
  --grey:#6a778b;
  --slate:#3e4c63;
  --slate-light:#5d6a82;
  --canvas:#ffffff;
}
*{margin:0;padding:0;box-sizing:border-box}
html,body{width:1200px;height:548px;overflow:hidden;background:var(--canvas);font-family:"Poppins",sans-serif}
.board{position:relative;width:1200px;height:548px}
.variant-label{position:absolute;top:2px;width:183px;text-align:center;font-size:3.2px;font-weight:600;color:var(--ink)}
.page{position:absolute;top:12px;width:392px;height:1151px;overflow:hidden;
  background:linear-gradient(180deg,var(--blue-dark),var(--blue) 70%);
  transform:scale(.4665);transform-origin:0 0;box-shadow:0 0 4px rgba(0,0,0,.15)}
.topbar{position:absolute;top:0;left:0;width:392px;height:30px;background:var(--white);display:flex;align-items:center;padding:0 30px}
.brand{font-size:15px;font-weight:400;color:var(--grey);letter-spacing:-.2px}
.nav{display:flex;gap:9px;margin-left:auto;font-size:4px;font-weight:600;color:var(--ink)}
.nav-cta{margin-left:12px;background:var(--yellow);color:var(--white);font-size:4px;font-weight:700;padding:4px 10px;border-radius:8px}
.waves{position:absolute;top:0;left:0}
.title{position:absolute;color:var(--white);font-size:14px;font-weight:700}
.title.story{left:30px;top:46px}
.title.values{left:255px;top:186px}
.milestone{position:absolute;color:var(--white)}
.years{display:flex;justify-content:space-between;font-size:5px;font-weight:700}
.track{position:relative;height:6px;margin:2px 0 5px}
.track::before{content:"";position:absolute;left:3px;right:3px;top:2.5px;height:1px;background:var(--white)}
.track i{position:absolute;top:0;width:6px;height:6px;border:1px solid var(--white);border-radius:50%;background:var(--blue-dark)}
.track i:last-child{right:0}
.milestone ul{list-style:none;font-size:3.4px;line-height:6px}
.milestone li::before{content:"";display:inline-block;width:2.5px;height:2.5px;border-radius:50%;background:var(--yellow);margin-right:3px;vertical-align:middle}
.gold .years{color:var(--yellow)}
.gold .years span:first-child{color:var(--yellow)}
.boxed ul{padding:6px;border-radius:2px;background:var(--blue-light);color:var(--blue-dark)}
.boxed.alt ul{background:var(--yellow);color:var(--white)}
.boxed.mute ul{background:#c9d6e4;color:var(--white)}
.value{position:absolute;display:flex;align-items:flex-start;gap:14px;width:300px}
.art{flex:none;width:64px;height:58px;border-radius:12px;background:linear-gradient(135deg,var(--blue-light),#8fb1d8 60%,var(--yellow))}
.value h3{font-size:7px;font-weight:700;color:var(--ink);line-height:8px;margin-top:4px}
.value p{font-size:3.6px;line-height:5.2px;color:var(--grey);width:140px;margin-top:3px}
.newsletter{position:absolute;left:45px;top:935px;width:300px;height:66px;border-radius:33px;background:var(--yellow);display:flex;align-items:center;padding:0 24px;gap:18px}
.newsletter h4{font-size:9.5px;font-weight:700;color:var(--white)}
.newsletter p{font-size:4px;font-weight:600;color:var(--white);line-height:5px;margin-top:2px;width:140px}
.field{flex:none;width:100px;height:15px;border-radius:8px;background:var(--white);display:flex;align-items:center;justify-content:space-between;padding:0 3px 0 8px;font-size:3.5px;color:var(--grey)}
.field b{width:10px;height:10px;border-radius:50%;background:var(--slate-light)}
.footer{position:absolute;left:0;top:1035px;width:392px;display:flex;padding:0 40px;color:var(--white)}
.footer-brand{width:120px}
.footer-brand .brand{color:var(--white);font-size:20px}
.socials{display:flex;gap:4px;margin:6px 0 0 16px}
.socials i{width:11px;height:11px;border-radius:50%;background:var(--slate-light);border:1px solid #8a96aa}
.footer-cta{display:inline-block;margin:10px 0 0 28px;background:var(--yellow);font-size:3.6px;font-weight:700;padding:3px 9px;border-radius:6px}
.col{font-size:3.4px;line-height:9px;margin-right:16px}
.col h5{font-size:5px;font-weight:700;line-height:8px;margin-bottom:2px}
.chat{position:absolute;right:14px;bottom:4px;width:12px;height:12px;border-radius:50%;background:var(--yellow)}
</style>
</head>
<body>
<div class="board">

<!-- column template repeated six times -->
<div class="variant-label" style="left:15px">Variant 1</div>
<div class="page" style="left:15px">
  <div class="topbar"><span class="brand">Veltrano</span><nav class="nav"><span>ABOUT US</span><span>SERVICES</span><span>INSIGHTS</span><span>JOIN US</span></nav><span class="nav-cta">CONTACT US</span></div>
  <svg class="waves" width="392" height="1151" viewBox="0 0 392 1151"><path d="M0 645C40 600 55 400 72 300C95 235 210 228 392 205L392 580C338 640 318 780 350 880C368 925 392 932 392 940L392 1000L0 1000Z" fill="#fff"/><path d="M0 975C80 958 125 1010 200 1000C280 990 330 958 392 985L392 1151L0 1151Z" fill="#4a5870"/></svg>
  <h2 class="title story">Our Story</h2>
  <div class="milestone" style="left:30px;top:108px;width:80px"><div class="years"><span>2017</span><span>2018</span></div><div class="track"><i></i><i></i></div><ul><li>Growth Strategy Focus</li><li>Consistent, Modest Growth</li><li>Preliminary Focus on Technology</li><li>Eureka! Implementing strategy is hard</li></ul></div>
  <div class="milestone" style="left:155px;top:92px;width:75px"><div class="years"><span>2020</span><span>2021</span></div><div class="track"><i></i><i></i></div><ul><li>Pandemic Pauses Growth</li><li>Rethinking</li><li>the business model</li><li>the delivery model</li></ul></div>
  <div class="milestone" style="left:282px;top:72px;width:80px"><div class="years"><span>2022</span><span>Onward</span></div><div class="track"><i></i><i></i></div><ul><li>Leadership Team for Focus on Essential Areas</li><li>Rapid Growth</li><li>Customer Success</li></ul></div>
  <h2 class="title values">Our Values</h2>
  <div class="value" style="left:55px;top:255px"><div class="art" role="img" aria-label="Illustration of a diverse group of people around a globe"></div><div><h3>The Value of Every Human.<br>Regardless.</h3><p>Each person's unique experiences and perspectives add vibrant hues to our shared existence.</p></div></div>
  <div class="value" style="left:85px;top:350px"><div class="art" role="img" aria-label="Illustration of people fitting puzzle pieces together"></div><div><h3>Collaboration</h3><p>Collaboration transforms individual endeavors into symphonies of collective achievement and shared success.</p></div></div>
  <div class="value" style="left:140px;top:445px"><div class="art" role="img" aria-label="Illustration of a rocket launching"></div><div><h3>Passion</h3><p>Passion infuses our work with energy, turning routine tasks into chances to innovate.</p></div></div>
  <div class="value" style="left:112px;top:536px"><div class="art" role="img" aria-label="Illustration of a team climbing toward a flag"></div><div><h3>Excellence</h3><p>Excellence is a continuous journey of refinement, growth and lasting impact beyond tasks.</p></div></div>
  <div class="value" style="left:85px;top:630px"><div class="art" role="img" aria-label="Illustration of a target on a screen with charts"></div><div><h3>Tenacity</h3><p>Tenacity keeps us grounded amid adversity and propels us forward through every obstacle.</p></div></div>
  <div class="value" style="left:55px;top:723px"><div class="art" role="img" aria-label="Illustration of a brain with a lightbulb"></div><div><h3>Solution Mindset</h3><p>A solution mindset turns problems into possibilities and paves the way for growth.</p></div></div>
  <div class="value" style="left:85px;top:818px"><div class="art" role="img" aria-label="Illustration of people sharing ideas around a device"></div><div><h3>Generosity</h3><p>Generosity creates a cycle of goodwill, fostering unity and shared purpose among colleagues.</p></div></div>
  <div class="newsletter"><div><h4>Subscribe Our Newsletter</h4><p>Subscribe our newsletter to receive the latest news and exclusive offers every week. No spam.</p></div><div class="field">Enter email address<b></b></div></div>
  <div class="footer"><div class="footer-brand"><span class="brand">Veltrano</span><div class="socials"><i></i><i></i><i></i><i></i></div><span class="footer-cta">CONTACT US</span></div><div class="col"><h5>Quick links</h5>Home<br>About Us<br>Services<br>Insights<br>Join Us<br>Contact Us</div><div class="col"><h5>Our Services</h5>Business Transformation<br>ERP Implementations<br>ERP Solutions<br>BI and Data<br>Building the Right Team</div><div class="col"><h5>Contact info</h5>Email<br>hello@veltrano.com<br>Phone<br>+44 20 4960 0312<br>Location<br>Some address line goes here</div></div>
  <span class="chat"></span>
</div>

<div class="variant-label" style="left:212px">Variant 2</div>
<div class="page" style="left:212px">
  <div class="topbar"><span class="brand">Veltrano</span><nav class="nav"><span>ABOUT US</span><span>SERVICES</span><span>INSIGHTS</span><span>JOIN US</span></nav><span class="nav-cta">CONTACT US</span></div>
  <svg class="waves" width="392" height="1151" viewBox="0 0 392 1151"><path d="M0 645C40 600 55 400 72 300C95 235 210 228 392 205L392 580C338 640 318 780 350 880C368 925 392 932 392 940L392 1000L0 1000Z" fill="#fff"/><path d="M0 975C80 958 125 1010 200 1000C280 990 330 958 392 985L392 1151L0 1151Z" fill="#4a5870"/></svg>
  <h2 class="title story">Our Story</h2>
  <div class="milestone" style="left:30px;top:108px;width:80px"><div class="years"><span>2017</span><span>2018</span></div><div class="track"><i></i><i></i></div><ul><li>Growth Strategy Focus</li><li>Consistent, Modest Growth</li><li>Preliminary Focus on Technology</li><li>Eureka! Implementing strategy is hard</li></ul></div>
  <div class="milestone" style="left:155px;top:92px;width:75px"><div class="years"><span>2020</span><span>2021</span></div><div class="track"><i></i><i></i></div><ul><li>Pandemic Pauses Growth</li><li>Rethinking</li><li>the business model</li><li>the delivery model</li></ul></div>
  <div class="milestone" style="left:282px;top:80px;width:80px"><div class="years"><span>2022</span><span>Onward</span></div><div class="track"><i></i><i></i></div><ul><li>Leadership Team for Focus on Essential Areas</li><li>Rapid Growth</li><li>Customer Success</li></ul></div>
  <h2 class="title values">Our Values</h2>
  <div class="value" style="left:55px;top:255px"><div class="art" role="img" aria-label="Illustration of a diverse group of people around a globe"></div><div><h3>The Value of Every Human.<br>Regardless.</h3><p>Each person's unique experiences and perspectives add vibrant hues to our shared existence.</p></div></div>
  <div class="value" style="left:85px;top:350px"><div class="art" role="img" aria-label="Illustration of people fitting puzzle pieces together"></div><div><h3>Collaboration</h3><p>Collaboration transforms individual endeavors into symphonies of collective achievement and shared success.</p></div></div>
  <div class="value" style="left:140px;top:445px"><div class="art" role="img" aria-label="Illustration of a rocket launching"></div><div><h3>Passion</h3><p>Passion infuses our work with energy, turning routine tasks into chances to innovate.</p></div></div>
  <div class="value" style="left:112px;top:536px"><div class="art" role="img" aria-label="Illustration of a team climbing toward a flag"></div><div><h3>Excellence</h3><p>Excellence is a continuous journey of refinement, growth and lasting impact beyond tasks.</p></div></div>
  <div class="value" style="left:85px;top:630px"><div class="art" role="img" aria-label="Illustration of a target on a screen with charts"></div><div><h3>Tenacity</h3><p>Tenacity keeps us grounded amid adversity and propels us forward through every obstacle.</p></div></div>
  <div class="value" style="left:55px;top:723px"><div class="art" role="img" aria-label="Illustration of a brain with a lightbulb"></div><div><h3>Solution Mindset</h3><p>A solution mindset turns problems into possibilities and paves the way for growth.</p></div></div>
  <div class="value" style="left:85px;top:818px"><div class="art" role="img" aria-label="Illustration of people sharing ideas around a device"></div><div><h3>Generosity</h3><p>Generosity creates a cycle of goodwill, fostering unity and shared purpose among colleagues.</p></div></div>
  <div class="newsletter"><div><h4>Subscribe Our Newsletter</h4><p>Subscribe our newsletter to receive the latest news and exclusive offers every week. No spam.</p></div><div class="field">Enter email address<b></b></div></div>
  <div class="footer"><div class="footer-brand"><span class="brand">Veltrano</span><div class="socials"><i></i><i></i><i></i><i></i></div><span class="footer-cta">CONTACT US</span></div><div class="col"><h5>Quick links</h5>Home<br>About Us<br>Services<br>Insights<br>Join Us<br>Contact Us</div><div class="col"><h5>Our Services</h5>Business Transformation<br>ERP Implementations<br>ERP Solutions<br>BI and Data<br>Building the Right Team</div><div class="col"><h5>Contact info</h5>Email<br>hello@veltrano.com<br>Phone<br>+44 20 4960 0312<br>Location<br>Some address line goes here</div></div>
  <span class="chat"></span>
</div>

<div class="variant-label" style="left:410px">Variant 3</div>
<div class="page" style="left:410px">
  <div class="topbar"><span class="brand">Veltrano</span><nav class="nav"><span>ABOUT US</span><span>SERVICES</span><span>INSIGHTS</span><span>JOIN US</span></nav><span class="nav-cta">CONTACT US</span></div>
  <svg class="waves" width="392" height="1151" viewBox="0 0 392 1151"><path d="M0 645C40 600 55 400 72 300C95 235 210 228 392 205L392 580C338 640 318 780 350 880C368 925 392 932 392 940L392 1000L0 1000Z" fill="#fff"/><path d="M0 975C80 958 125 1010 200 1000C280 990 330 958 392 985L392 1151L0 1151Z" fill="#4a5870"/></svg>
  <h2 class="title story">Our Story</h2>
  <div class="milestone" style="left:30px;top:104px;width:90px"><div class="years"><span>2017</span><span>2018</span></div><div class="track"><i></i><i></i></div><ul><li>Growth Strategy Focus</li><li>Consistent, Modest Growth</li><li>Preliminary Focus on Technology</li><li>Eureka! Implementing strategy is hard</li></ul></div>
  <div class="milestone" style="left:165px;top:92px;width:60px"><div class="years"><span>2020</span><span>2021</span></div><div class="track"><i></i><i></i></div><ul><li>Pandemic Pauses Growth</li><li>Rethinking</li><li>the business model</li><li>the delivery model</li></ul></div>
  <div class="milestone" style="left:255px;top:80px;width:105px"><div class="years"><span>2022</span><span>Onward</span></div><div class="track"><i></i><i></i></div><ul><li>Leadership Team for Focus on Essential Areas</li><li>Rapid Growth</li><li>Customer Success</li></ul></div>
  <h2 class="title values">Our Values</h2>
  <div class="value" style="left:55px;top:255px"><div class="art" role="img" aria-label="Illustration of a diverse group of people around a globe"></div><div><h3>The Value of Every Human.<br>Regardless.</h3><p>Each person's unique experiences and perspectives add vibrant hues to our shared existence.</p></div></div>
  <div class="value" style="left:85px;top:350px"><div class="art" role="img" aria-label="Illustration of people fitting puzzle pieces together"></div><div><h3>Collaboration</h3><p>Collaboration transforms individual endeavors into symphonies of collective achievement and shared success.</p></div></div>
  <div class="value" style="left:140px;top:445px"><div class="art" role="img" aria-label="Illustration of a rocket launching"></div><div><h3>Passion</h3><p>Passion infuses our work with energy, turning routine tasks into chances to innovate.</p></div></div>
  <div class="value" style="left:112px;top:536px"><div class="art" role="img" aria-label="Illustration of a team climbing toward a flag"></div><div><h3>Excellence</h3><p>Excellence is a continuous journey of refinement, growth and lasting impact beyond tasks.</p></div></div>
  <div class="value" style="left:85px;top:630px"><div class="art" role="img" aria-label="Illustration of a target on a screen with charts"></div><div><h3>Tenacity</h3><p>Tenacity keeps us grounded amid adversity and propels us forward through every obstacle.</p></div></div>
  <div class="value" style="left:55px;top:723px"><div class="art" role="img" aria-label="Illustration of a brain with a lightbulb"></div><div><h3>Solution Mindset</h3><p>A solution mindset turns problems into possibilities and paves the way for growth.</p></div></div>
  <div class="value" style="left:85px;top:818px"><div class="art" role="img" aria-label="Illustration of people sharing ideas around a device"></div><div><h3>Generosity</h3><p>Generosity creates a cycle of goodwill, fostering unity and shared purpose among colleagues.</p></div></div>
  <div class="newsletter"><div><h4>Subscribe Our Newsletter</h4><p>Subscribe our newsletter to receive the latest news and exclusive offers every week. No spam.</p></div><div class="field">Enter email address<b></b></div></div>
  <div class="footer"><div class="footer-brand"><span class="brand">Veltrano</span><div class="socials"><i></i><i></i><i></i><i></i></div><span class="footer-cta">CONTACT US</span></div><div class="col"><h5>Quick links</h5>Home<br>About Us<br>Services<br>Insights<br>Join Us<br>Contact Us</div><div class="col"><h5>Our Services</h5>Business Transformation<br>ERP Implementations<br>ERP Solutions<br>BI and Data<br>Building the Right Team</div><div class="col"><h5>Contact info</h5>Email<br>hello@veltrano.com<br>Phone<br>+44 20 4960 0312<br>Location<br>Some address line goes here</div></div>
  <span class="chat"></span>
</div>

<div class="variant-label" style="left:607px">Variant 4</div>
<div class="page" style="left:607px">
  <div class="topbar"><span class="brand">Veltrano</span><nav class="nav"><span>ABOUT US</span><span>SERVICES</span><span>INSIGHTS</span><span>JOIN US</span></nav><span class="nav-cta">CONTACT US</span></div>
  <svg class="waves" width="392" height="1151" viewBox="0 0 392 1151"><path d="M0 645C40 600 55 400 72 300C95 235 210 228 392 205L392 580C338 640 318 780 350 880C368 925 392 932 392 940L392 1000L0 1000Z" fill="#fff"/><path d="M0 975C80 958 125 1010 200 1000C280 990 330 958 392 985L392 1151L0 1151Z" fill="#4a5870"/></svg>
  <h2 class="title story">Our Story</h2>
  <div class="milestone boxed" style="left:30px;top:94px;width:135px"><div class="years"><span>2017</span></div><div class="track"><i></i><i></i></div><ul><li>Growth Strategy Focus</li><li>Consistent, Modest Growth</li><li>Preliminary Focus on Technology</li><li>Eureka! Implementing strategy is hard</li></ul></div>
  <div class="milestone boxed alt" style="left:165px;top:78px;width:100px"><div class="years"><span>2020</span></div><div class="track"><i></i><i></i></div><ul><li>Pandemic Pauses Growth</li><li>Rethinking</li><li>the business model</li><li>the delivery model</li></ul></div>
  <div class="milestone boxed mute" style="left:265px;top:62px;width:105px"><div class="years"><span>2022</span><span>Onward</span></div><div class="track"><i></i><i></i></div><ul><li>Leadership Team for Focus on Essential Areas</li><li>Rapid Growth</li><li>Customer Success</li></ul></div>
  <h2 class="title values">Our Values</h2>
  <div class="value" style="left:55px;top:255px"><div class="art" role="img" aria-label="Illustration of a diverse group of people around a globe"></div><div><h3>The Value of Every Human.<br>Regardless.</h3><p>Each person's unique experiences and perspectives add vibrant hues to our shared existence.</p></div></div>
  <div class="value" style="left:85px;top:350px"><div class="art" role="img" aria-label="Illustration of people fitting puzzle pieces together"></div><div><h3>Collaboration</h3><p>Collaboration transforms individual endeavors into symphonies of collective achievement and shared success.</p></div></div>
  <div class="value" style="left:140px;top:445px"><div class="art" role="img" aria-label="Illustration of a rocket launching"></div><div><h3>Passion</h3><p>Passion infuses our work with energy, turning routine tasks into chances to innovate.</p></div></div>
  <div class="value" style="left:112px;top:536px"><div class="art" role="img" aria-label="Illustration of a team climbing toward a flag"></div><div><h3>Excellence</h3><p>Excellence is a continuous journey of refinement, growth and lasting impact beyond tasks.</p></div></div>
  <div class="value" style="left:85px;top:630px"><div class="art" role="img" aria-label="Illustration of a target on a screen with charts"></div><div><h3>Tenacity</h3><p>Tenacity keeps us grounded amid adversity and propels us forward through every obstacle.</p></div></div>
  <div class="value" style="left:55px;top:723px"><div class="art" role="img" aria-label="Illustration of a brain with a lightbulb"></div><div><h3>Solution Mindset</h3><p>A solution mindset turns problems into possibilities and paves the way for growth.</p></div></div>
  <div class="value" style="left:85px;top:818px"><div class="art" role="img" aria-label="Illustration of people sharing ideas around a device"></div><div><h3>Generosity</h3><p>Generosity creates a cycle of goodwill, fostering unity and shared purpose among colleagues.</p></div></div>
  <div class="newsletter"><div><h4>Subscribe Our Newsletter</h4><p>Subscribe our newsletter to receive the latest news and exclusive offers every week. No spam.</p></div><div class="field">Enter email address<b></b></div></div>
  <div class="footer"><div class="footer-brand"><span class="brand">Veltrano</span><div class="socials"><i></i><i></i><i></i><i></i></div><span class="footer-cta">CONTACT US</span></div><div class="col"><h5>Quick links</h5>Home<br>About Us<br>Services<br>Insights<br>Join Us<br>Contact Us</div><div class="col"><h5>Our Services</h5>Business Transformation<br>ERP Implementations<br>ERP Solutions<br>BI and Data<br>Building the Right Team</div><div class="col"><h5>Contact info</h5>Email<br>hello@veltrano.com<br>Phone<br>+44 20 4960 0312<br>Location<br>Some address line goes here</div></div>
  <span class="chat"></span>
</div>

<div class="variant-label" style="left:805px">Variant 5</div>
<div class="page" style="left:805px">
  <div class="topbar"><span class="brand">Veltrano</span><nav class="nav"><span>ABOUT US</span><span>SERVICES</span><span>INSIGHTS</span><span>JOIN US</span></nav><span class="nav-cta">CONTACT US</span></div>
  <svg class="waves" width="392" height="1151" viewBox="0 0 392 1151"><path d="M0 665C45 620 60 420 80 330C105 260 215 248 392 225L392 600C338 660 318 800 350 900C368 935 392 940 392 945L392 1000L0 1000Z" fill="#fff"/><path d="M0 975C80 958 125 1010 200 1000C280 990 330 958 392 985L392 1151L0 1151Z" fill="#4a5870"/></svg>
  <h2 class="title story">Our Story</h2>
  <div class="milestone gold" style="left:30px;top:112px;width:90px"><div class="years"><span>2017</span><span>2018</span></div><div class="track"><i></i><i></i></div><ul><li>Growth Strategy Focus</li><li>Consistent, Modest Growth</li><li>Preliminary Focus on Technology</li><li>Eureka! Implementing strategy is hard</li></ul></div>
  <div class="milestone gold" style="left:160px;top:102px;width:65px"><div class="years"><span>2020</span><span>2021</span></div><div class="track"><i></i><i></i></div><ul><li>Pandemic Pauses Growth</li><li>Rethinking</li><li>the business model</li><li>the delivery model</li></ul></div>
  <div class="milestone gold" style="left:255px;top:90px;width:105px"><div class="years"><span>2022</span><span>Onward</span></div><div class="track"><i></i><i></i></div><ul><li>Leadership Team for Focus on Essential Areas</li><li>Rapid Growth</li><li>Customer Success</li></ul></div>
  <h2 class="title values" style="top:206px">Our Values</h2>
  <div class="value" style="left:55px;top:282px"><div class="art" role="img" aria-label="Illustration of a diverse group of people around a globe"></div><div><h3>The Value of Every Human.<br>Regardless.</h3><p>Each person's unique experiences and perspectives add vibrant hues to our shared existence.</p></div></div>
  <div class="value" style="left:85px;top:377px"><div class="art" role="img" aria-label="Illustration of people fitting puzzle pieces together"></div><div><h3>Collaboration</h3><p>Collaboration transforms individual endeavors into symphonies of collective achievement and shared success.</p></div></div>
  <div class="value" style="left:140px;top:472px"><div class="art" role="img" aria-label="Illustration of a rocket launching"></div><div><h3>Passion</h3><p>Passion infuses our work with energy, turning routine tasks into chances to innovate.</p></div></div>
  <div class="value" style="left:112px;top:565px"><div class="art" role="img" aria-label="Illustration of a team climbing toward a flag"></div><div><h3>Excellence</h3><p>Excellence is a continuous journey of refinement, growth and lasting impact beyond tasks.</p></div></div>
  <div class="value" style="left:85px;top:658px"><div class="art" role="img" aria-label="Illustration of a target on a screen with charts"></div><div><h3>Tenacity</h3><p>Tenacity keeps us grounded amid adversity and propels us forward through every obstacle.</p></div></div>
  <div class="value" style="left:55px;top:750px"><div class="art" role="img" aria-label="Illustration of a brain with a lightbulb"></div><div><h3>Solution Mindset</h3><p>A solution mindset turns problems into possibilities and paves the way for growth.</p></div></div>
  <div class="value" style="left:85px;top:845px"><div class="art" role="img" aria-label="Illustration of people sharing ideas around a device"></div><div><h3>Generosity</h3><p>Generosity creates a cycle of goodwill, fostering unity and shared purpose among colleagues.</p></div></div>
  <div class="newsletter"><div><h4>Subscribe Our Newsletter</h4><p>Subscribe our newsletter to receive the latest news and exclusive offers every week. No spam.</p></div><div class="field">Enter email address<b></b></div></div>
  <div class="footer"><div class="footer-brand"><span class="brand">Veltrano</span><div class="socials"><i></i><i></i><i></i><i></i></div><span class="footer-cta">CONTACT US</span></div><div class="col"><h5>Quick links</h5>Home<br>About Us<br>Services<br>Insights<br>Join Us<br>Contact Us</div><div class="col"><h5>Our Services</h5>Business Transformation<br>ERP Implementations<br>ERP Solutions<br>BI and Data<br>Building the Right Team</div><div class="col"><h5>Contact info</h5>Email<br>hello@veltrano.com<br>Phone<br>+44 20 4960 0312<br>Location<br>Some address line goes here</div></div>
  <span class="chat"></span>
</div>

<div class="variant-label" style="left:1002px">Variant 6</div>
<div class="page" style="left:1002px">
  <div class="topbar"><span class="brand">Veltrano</span><nav class="nav"><span>ABOUT US</span><span>SERVICES</span><span>INSIGHTS</span><span>JOIN US</span></nav><span class="nav-cta">CONTACT US</span></div>
  <svg class="waves" width="392" height="1151" viewBox="0 0 392 1151"><path d="M0 645C40 600 55 400 72 300C95 235 210 228 392 205L392 580C338 640 318 780 350 880C368 925 392 932 392 940L392 1010L0 1010Z" fill="#fff"/><path d="M0 990C80 972 125 1022 200 1012C280 1002 330 972 392 998L392 1151L0 1151Z" fill="#4a5870"/></svg>
  <h2 class="title story">Our Story</h2>
  <div class="milestone gold" style="left:30px;top:104px;width:80px"><div class="years"><span>2017</span><span style="color:#fff">2018</span></div><div class="track"><i></i><i></i></div><ul><li>Growth Strategy Focus</li><li>the business model</li><li>Preliminary Focus on Technology</li><li>Eureka! Implementing strategy is hard</li></ul></div>
  <div class="milestone" style="left:155px;top:92px;width:75px"><div class="years"><span>2020</span><span>2021</span></div><div class="track"><i></i><i></i></div><ul><li>Pandemic Pauses Growth</li><li>Rethinking</li><li>the business model</li><li>the delivery model</li></ul></div>
  <div class="milestone gold" style="left:282px;top:80px;width:80px"><div class="years"><span style="color:#fff">2022</span><span>Onward</span></div><div class="track"><i></i><i></i></div><ul><li>Leadership Team for Focus on Essential Areas</li><li>Rapid Growth</li><li>Customer Success</li></ul></div>
  <h2 class="title values" style="top:187px">Our Values</h2>
  <div class="value" style="left:55px;top:258px"><div class="art" role="img" aria-label="Illustration of a diverse group of people around a globe"></div><div><h3>The Value of Every Human.<br>Regardless.</h3><p>Each person's unique experiences and perspectives add vibrant hues to our shared existence.</p></div></div>
  <div class="value" style="left:85px;top:355px"><div class="art" role="img" aria-label="Illustration of people fitting puzzle pieces together"></div><div><h3>Collaboration</h3><p>Collaboration transforms individual endeavors into symphonies of collective achievement and shared success.</p></div></div>
  <div class="value" style="left:140px;top:450px"><div class="art" role="img" aria-label="Illustration of a rocket launching"></div><div><h3>Passion</h3><p>Passion infuses our work with energy, turning routine tasks into chances to innovate.</p></div></div>
  <div class="value" style="left:112px;top:545px"><div class="art" role="img" aria-label="Illustration of a team climbing toward a flag"></div><div><h3>Excellence</h3><p>Excellence is a continuous journey of refinement, growth and lasting impact beyond tasks.</p></div></div>
  <div class="value" style="left:85px;top:640px"><div class="art" role="img" aria-label="Illustration of a target on a screen with charts"></div><div><h3>Tenacity</h3><p>Tenacity keeps us grounded amid adversity and propels us forward through every obstacle.</p></div></div>
  <div class="value" style="left:55px;top:735px"><div class="art" role="img" aria-label="Illustration of a brain with a lightbulb"></div><div><h3>Solution Mindset</h3><p>A solution mindset turns problems into possibilities and paves the way for growth.</p></div></div>
  <div class="value" style="left:85px;top:830px"><div class="art" role="img" aria-label="Illustration of people sharing ideas around a device"></div><div><h3>Generosity</h3><p>Generosity creates a cycle of goodwill, fostering unity and shared purpose among colleagues.</p></div></div>
  <div class="newsletter" style="top:948px"><div><h4>Subscribe Our Newsletter</h4><p>Subscribe our newsletter to receive the latest news and exclusive offers every week. No spam.</p></div><div class="field">Enter email address<b></b></div></div>
  <div class="footer" style="top:1048px"><div class="footer-brand"><span class="brand">Veltrano</span><div class="socials"><i></i><i></i><i></i><i></i></div><span class="footer-cta">CONTACT US</span></div><div class="col"><h5>Quick links</h5>Home<br>About Us<br>Services<br>Insights<br>Join Us<br>Contact Us</div><div class="col"><h5>Our Services</h5>Business Transformation<br>ERP Implementations<br>ERP Solutions<br>BI and Data<br>Building the Right Team</div><div class="col"><h5>Contact info</h5>Email<br>hello@veltrano.com<br>Phone<br>+44 20 4960 0312<br>Location<br>Some address line goes here</div></div>
</div>

</div>
</body>
</html>
```